Existing Website Requiring new Pages

I have an existing word press website that was built using elementor.
Website: www.tallowcrestcare.com.au
I require the Vacancies page (https://www.tallowcrestcare.com.au/vacancies/) to be modified to display our new properties along with minor tweaks to how the information is presented.
The vacancies to be displayed are the exactly the same as those that are located on the homepage of QMR website (https://qmr.org.au/)
The new pages that link off the Vacancies tab will require custom design.
There are roughly 8 pages/properties to be incorporated. i wish for the design to be very similar to that displayed in the following link; https://www.polunda.com.au/vacancies/merrylands
Along with this the back end has not been updated for the last 3 years so it also requires some maintenance.
Website is in the disability industry and the custom pages will display information relative to Property Vacancies.
I have attached a ZIP file with some design guides, the information for each of the properties (which will need to be modified to show our business name Tallowcrest Care) and the example of how it is to look based off the Polunda website.
If you guys have any suggestions or ideas on how to make this more presentable or possible i'm open to your ideas.
Target Market(s)
People looking for SDA properties custom built for people with a disability
Industry/Entity Type
Disability
Coding
Coded - Design and coding required
Number of Pages Required
5+ page

```html
<!DOCTYPE html>
<html lang="en">
<head>
<meta charset="utf-8">
<title>Vacancies – Tallowcrest Care</title>
<link href="https://fonts.googleapis.com/css2?family=Montserrat:wght@400;500;600;700&display=swap" rel="stylesheet">
<style>
:root{
  --ink:#1d1d1d;
  --muted:#8a8a8a;
  --accent:#f39221;
  --blue:#2a8fd6;
  --line:#e4e4e4;
  --dark:#232323;
  --white:#ffffff;
}
*{box-sizing:border-box;margin:0;padding:0}
html,body{width:1200px;height:2847px;overflow:hidden;background:var(--white);font-family:'Montserrat',sans-serif;color:var(--ink)}
.page{position:relative;width:1200px;height:2847px}
.site-header{position:absolute;left:0;top:0;width:1200px;height:153px}
.brand{position:absolute;left:111px;top:40px;display:flex;align-items:center;gap:10px;font-size:22px;font-weight:600;color:var(--accent)}
.brand i{width:18px;height:18px;border-radius:50%;background:var(--accent);display:block}
.nav{position:absolute;top:72px;left:499px;display:flex;gap:0;font-size:13px;font-weight:500;letter-spacing:.2px}
.nav a{color:var(--ink);text-decoration:none;position:absolute;white-space:nowrap}
.nav a.active{color:var(--accent)}
.hero{position:absolute;left:0;top:153px;width:1200px;height:467px;background:linear-gradient(100deg,#6b3a12 0%,#b8661d 30%,#d9912f 50%,#8a4a1c 75%,#a62b1c 100%)}
.hero::after{content:"";position:absolute;inset:0;background:linear-gradient(90deg,rgba(0,0,0,.35),rgba(0,0,0,.05) 60%,rgba(0,0,0,.2))}
.hero h1{position:absolute;left:111px;top:195px;font-size:66px;font-weight:700;color:var(--white);z-index:1;letter-spacing:-.5px}
.hero-rule{position:absolute;top:618px;height:2px;background:var(--accent)}
.card{position:absolute;width:477px;height:410px;background:var(--white);box-shadow:0 2px 10px rgba(0,0,0,.09)}
.card .photo{position:absolute;left:17px;top:17px;width:443px;height:293px}
.card h2{position:absolute;left:21px;top:331px;font-size:25px;font-weight:600;letter-spacing:.2px}
.card .meta{position:absolute;right:17px;top:336px;display:flex;align-items:center;gap:14px;font-size:16px;font-weight:500}
.card .go{position:absolute;right:19px;top:372px}
.site-footer{position:absolute;left:0;top:2490px;width:1200px;height:307px;box-shadow:0 -8px 14px -10px rgba(0,0,0,.1)}
.foot-brand{position:absolute;left:122px;top:100px;display:flex;align-items:center;gap:10px;font-size:22px;font-weight:600;color:var(--accent)}
.foot-brand i{width:18px;height:18px;border-radius:50%;background:var(--accent);display:block}
.contact{position:absolute;left:120px;top:196px;font-size:12.5px;color:var(--muted);line-height:22px}
.contact li{list-style:none;display:flex;align-items:center;gap:9px}
.social{position:absolute;left:524px;top:54px}
.social span{display:block;width:32px;height:32px;border-radius:50%;margin-bottom:9px}
.col{position:absolute;top:50px;width:224px}
.col h3{font-size:14px;font-weight:500;border-left:2px solid var(--blue);padding-left:14px;height:16px;line-height:16px;margin-bottom:20px}
.col li{list-style:none;font-size:12.5px;color:var(--muted);line-height:22px;padding:4px 0 6px;border-top:1px solid var(--line)}
.col li:last-child{border-bottom:1px solid var(--line)}
.bottom-bar{position:absolute;left:0;top:2797px;width:1200px;height:50px;background:var(--dark);color:var(--white);font-size:12.5px;text-align:center;line-height:50px}
</style>
</head>
<body>
<div class="page">
<header class="site-header">
  <div class="brand"><i></i>Tallowcrest Care</div>
  <nav class="nav">
    <a style="left:0">HOME</a>
    <a style="left:67px">ABOUT US</a>
    <a class="active" style="left:160px">WHAT WE DO <svg width="14" height="9" viewBox="0 0 14 9"><path d="M1 1l6 6 6-6" fill="none" stroke="#f39221" stroke-width="1.6"/></svg></a>
    <a style="left:290px">REFERRALS</a>
    <a style="left:400px">FEEDBACK</a>
    <a style="left:500px">CONTACT US</a>
  </nav>
</header>

<section class="hero" role="img" aria-label="Person in a wheelchair in an autumn park with orange trees">
  <h1>Vacancies</h1>
</section>
<div class="hero-rule" style="left:0;width:111px"></div>
<div class="hero-rule" style="left:346px;width:30px"></div>

<main>
<svg width="0" height="0" style="position:absolute">
  <symbol id="bed" viewBox="0 0 36 24"><g fill="none" stroke="#1d1d1d" stroke-width="1.5"><rect x="4" y="2" width="28" height="10" rx="1"/><rect x="8" y="6" width="8" height="5"/><rect x="20" y="6" width="8" height="5"/><rect x="1" y="12" width="34" height="7" rx="1"/><path d="M4 19v3M32 19v3"/></g></symbol>
  <symbol id="arrow" viewBox="0 0 26 16"><path d="M0 8h24M17 1l7 7-7 7" fill="none" stroke="#8a8a8a" stroke-width="1.4"/></symbol>
</svg>

<article class="card" style="left:111px;top:705px"><div class="photo" role="img" aria-label="Two-storey brick house in Penrith" style="background:linear-gradient(#3f7fcf,#9cc3e6 55%,#8a5a3e 56%,#5d7a3a 85%,#444)"></div><h2>Penrith</h2><div class="meta"><svg width="36" height="24"><use href="#bed"/></svg>4 Bedroom SIL Home</div><svg class="go" width="26" height="16"><use href="#arrow"/></svg></article>
<article class="card" style="left:612px;top:705px"><div class="photo" role="img" aria-label="Timber cottages with access ramp in Mount Druitt" style="background:linear-gradient(#e9ecef,#c9b8a0 45%,#9a6d4e 60%,#6b9a3a 80%,#5d8a30)"></div><h2>Mount Druitt</h2><div class="meta"><svg width="36" height="24"><use href="#bed"/></svg>4 Bedroom SIL Home</div><svg class="go" width="26" height="16"><use href="#arrow"/></svg></article>

<article class="card" style="left:111px;top:1133px"><div class="photo" role="img" aria-label="Single-storey cream brick house in Casula" style="background:linear-gradient(#4d9ee0,#a9d2f0 40%,#e3d6b0 55%,#cbbf9e 75%,#8fa860)"></div><h2>Casula</h2><div class="meta"><svg width="36" height="24"><use href="#bed"/></svg>4 Bedroom SIL Home</div><svg class="go" width="26" height="16"><use href="#arrow"/></svg></article>
<article class="card" style="left:612px;top:1133px"><div class="photo" role="img" aria-label="Dark timber house with chimneys in Eastwood" style="background:linear-gradient(#4b8ed8,#c8dcef 30%,#2a2a2a 50%,#3a3a30 70%,#3f6a2a)"></div><h2>Eastwood</h2><div class="meta"><svg width="36" height="24"><use href="#bed"/></svg>4 Bedroom SIL Home</div><svg class="go" width="26" height="16"><use href="#arrow"/></svg></article>

<article class="card" style="left:111px;top:1560px"><div class="photo" role="img" aria-label="Brick house with double garage in Baulkham Hills" style="background:linear-gradient(#5aa3e0,#c2ddf2 40%,#b9a58a 55%,#6aa33a 75%,#c9a98a)"></div><h2>Baulkham Hills</h2><div class="meta"><svg width="36" height="24"><use href="#bed"/></svg>4 Bedroom SIL Home</div><svg class="go" width="26" height="16"><use href="#arrow"/></svg></article>
<article class="card" style="left:612px;top:1560px"><div class="photo" role="img" aria-label="Orange brick house with driveway in Merrylands" style="background:linear-gradient(#5aa3e0,#c7e0f2 38%,#c4643a 50%,#7ab83c 70%,#c8c4bc)"></div><h2>Merrylands</h2><div class="meta"><svg width="36" height="24"><use href="#bed"/></svg>4 Bedroom SIL Home</div><svg class="go" width="26" height="16"><use href="#arrow"/></svg></article>

<article class="card" style="left:111px;top:1988px"><div class="photo" role="img" aria-label="Large heritage house on lawn in Parramatta" style="background:linear-gradient(#4f93d8,#bcd6ee 35%,#d9cfb5 55%,#7ea546 72%,#6a9a3a)"></div><h2>Parramatta</h2><div class="meta"><svg width="36" height="24"><use href="#bed"/></svg>4 Bedroom SIL Home</div><svg class="go" width="26" height="16"><use href="#arrow"/></svg></article>
<article class="card" style="left:612px;top:1988px"><div class="photo" role="img" aria-label="White weatherboard house with veranda in Cabramatta" style="background:linear-gradient(#2f7fd0,#d6e6f4 35%,#f2f2f0 55%,#5a8a35 75%,#7aa84a)"></div><h2>Cabramatta</h2><div class="meta"><svg width="36" height="24"><use href="#bed"/></svg>4 Bedroom SIL Home</div><svg class="go" width="26" height="16"><use href="#arrow"/></svg></article>
</main>

<footer class="site-footer">
  <div class="foot-brand"><i></i>Tallowcrest Care</div>
  <ul class="contact">
    <li><svg width="13" height="10" viewBox="0 0 13 10"><rect x=".7" y=".7" width="11.6" height="8.6" fill="none" stroke="#e5467a" stroke-width="1.2"/><path d="M1 1l5.5 4.5L12 1" fill="none" stroke="#e5467a" stroke-width="1.2"/></svg>Email: info@tallowcrestcare.com.au</li>
    <li><svg width="13" height="13" viewBox="0 0 24 24"><path d="M6.6 10.8a15 15 0 006.6 6.6l2.2-2.2a1 1 0 011-.25 11 11 0 003.6.6 1 1 0 011 1V20a1 1 0 01-1 1A17 17 0 013 4a1 1 0 011-1h3.5a1 1 0 011 1 11 11 0 00.6 3.6 1 1 0 01-.25 1z" fill="#e5467a"/></svg>Phone: +61 0400 123 456</li>
    <li><svg width="13" height="13" viewBox="0 0 14 14"><circle cx="7" cy="7" r="6" fill="none" stroke="#e5467a" stroke-width="1.3"/><path d="M7 3.5V7l2.5 1.5" fill="none" stroke="#e5467a" stroke-width="1.3"/></svg>Operating Hours: 9AM To 5PM Monday - Friday</li>
  </ul>
  <div class="social">
    <span style="background:#6b2c8f"></span>
    <span style="background:#1c5fa8"></span>
    <span style="background:#222"></span>
    <span style="background:#1c6fb0"></span>
  </div>
  <div class="col" style="left:614px">
    <h3>ACCOMMODATION</h3>
    <ul><li>Supported Independent Living (SIL)</li><li>Specialist Disability Accommodation (SDA)</li><li>Short term Accommodation (Respite)</li><li>Vacancies</li></ul>
  </div>
  <div class="col" style="left:861px">
    <h3>WHAT WE DO</h3>
    <ul><li>In Home Care</li><li>Social &amp; Community Services</li><li>Therapeutic Supports</li><li>Support Coordination</li><li>Home Modifications</li></ul>
  </div>
</footer>
<div class="bottom-bar">© Copyright 2024 | Tallowcrest Care | All Rights Reserved.</div>
</div>
</body>
</html>
```